Harborview Estates Business Card for Apartment Buildings

Create business cards for resident managers who run apartment buildings. The audience is the public who are searching for apartment rentals, and current residents who live at the apartment building. Key design element will be incorporating the company logo, however, the logo cannot dominate. The building name and manager name are more important than the logo. Current business card design leaves little room for copy, so we may need to reduce the size on the current card to allow for more space for copy.

Target Market(s)

Adults 18-65 years of age, who are looking for an apartment rental, plus current residents who live at our apartment buildings.

Industry/Entity Type

Property Management

Contact Information for Business Card

A major design element will be use of the company logo. Important property and manager contact information must be part of the design. The size of the logo will need to be reduced to make room for building and manager contact copy.

Font styles to use
Sans Serif

Colors
3176b5
000000
959595
ffffff

Requirements
Must have
• 1) Incorporate the company logo.
• 2) Use the company colors (dark blue, black/grey, over white).
• 3) FEATURE THE BUILDING NAME
• 4) FEATURE THE MANAGER NAME
• 5) The company name is less important than BUILDING and MANAGER
• 6) Manager contact information
• **SEE ATTACHED CREATIVE BRIEF**
Nice to have
• 1) Back of card logo watermark
• 2) Ability to write notes on back of carfd
Should not have
• Avoid letting the company logo dominate the card, the building name and manager are more important than the company logo.

```html
<!DOCTYPE html>
<html lang="en">
<head>
<meta charset="utf-8">
<title>Harborview Estates – Resident Manager Business Card</title>
<link rel="stylesheet" href="https://fonts.googleapis.com/css2?family=Work+Sans:wght@400;500;600&display=swap">
<style>
  :root {
    --brand-blue: #3176b5;
    --ink: #000000;
    --stone: #959595;
    --paper: #ffffff;
    --card: #232323;
    --stage: #141414;
  }
  * { box-sizing: border-box; margin: 0; padding: 0; }
  html, body {
    width: 1200px; height: 900px; overflow: hidden;
    background: var(--stage);
    font-family: "Work Sans", Arial, sans-serif;
    color: var(--paper);
  }
  .canvas {
    position: relative; width: 1200px; height: 900px;
    display: flex; flex-direction: column; align-items: center; justify-content: center; gap: 40px;
  }
  .card {
    position: relative; width: 700px; height: 400px;
    background: var(--card);
    box-shadow: 0 10px 30px rgba(0,0,0,.6);
  }
  /* Front */
  .card--front { display: flex; flex-direction: column; align-items: center; justify-content: center; }
  .front-brand {
    display: flex; align-items: center; gap: 18px;
    font-weight: 600; font-size: 40px; letter-spacing: 2px;
    color: var(--stone); text-transform: uppercase;
  }
  .brand-dot { width: 44px; height: 44px; border-radius: 50%; background: var(--stone); }
  .front-url {
    position: absolute; bottom: 48px; left: 0; right: 0; text-align: center;
    font-size: 17px; letter-spacing: 3px; color: var(--paper);
  }
  .url-accent { color: var(--brand-blue); }
  /* Back */
  .card--back { display: flex; align-items: center; padding: 0 40px 0 40px; }
  .back-brand {
    width: 270px; display: flex; flex-direction: column; align-items: center; gap: 16px;
    font-weight: 600; font-size: 24px; letter-spacing: 1.5px; text-align: center;
    color: var(--paper); text-transform: uppercase;
  }
  .back-brand .brand-dot { width: 70px; height: 70px; background: var(--brand-blue); }
  .divider { width: 2px; height: 260px; background: var(--brand-blue); margin: 0 32px 0 20px; }
  .contact { flex: 1; }
  .manager-name {
    color: var(--brand-blue); font-weight: 500; font-size: 27px; letter-spacing: 1.5px; text-transform: uppercase;
  }
  .manager-role { font-size: 18px; letter-spacing: 1px; margin-top: 2px; }
  .building-name {
    color: var(--brand-blue); font-weight: 500; font-size: 17px; letter-spacing: 1px;
    text-transform: uppercase; margin-top: 14px;
  }
  .address { font-size: 17px; letter-spacing: 1px; line-height: 1.3; }
  .contact-list { list-style: none; margin-top: 16px; }
  .contact-list li {
    display: flex; align-items: center; gap: 16px;
    font-size: 18px; letter-spacing: 1px; line-height: 1.55;
  }
  .contact-list svg { width: 16px; height: 16px; fill: var(--brand-blue); flex: none; }
</style>
</head>
<body>
<main class="canvas">
  <section class="card card--front" aria-label="Card front">
    <div class="front-brand"><span class="brand-dot"></span>Harborview Estates</div>
    <p class="front-url">www.<span class="url-accent">harborviewest</span>.com</p>
  </section>

  <section class="card card--back" aria-label="Card back">
    <div class="back-brand"><span class="brand-dot"></span>Harborview<br>Estates</div>
    <div class="divider"></div>
    <div class="contact">
      <h1 class="manager-name">Marisol Ortega</h1>
      <p class="manager-role">Resident Manager</p>
      <h2 class="building-name">Cedar Court Apartments</h2>
      <p class="address">2485 Linden Avenue<br>Bayside, CA 90417</p>
      <ul class="contact-list">
        <li><svg viewBox="0 0 16 16" aria-hidden="true"><path d="M3 1l3 3-2 2c1 2 4 5 6 6l2-2 3 3-2 2C7 15 1 9 1 3z"/></svg>555-210-4830</li>
        <li><svg viewBox="0 0 16 16" aria-hidden="true"><rect x="4" y="1" width="8" height="4"/><rect x="1" y="6" width="14" height="6" rx="1"/><rect x="4" y="10" width="8" height="5"/></svg>555-210-4831</li>
        <li><svg viewBox="0 0 16 16" aria-hidden="true"><path d="M4 0h8v16H4zM5.5 2v10h5V2z"/></svg>555-388-9024</li>
        <li><svg viewBox="0 0 16 16" aria-hidden="true"><path d="M0 3h16v1L8 9 0 4zM0 6l8 5 8-5v7H0z"/></svg>marisol@harborviewest.com</li>
        <li><svg viewBox="0 0 16 16" aria-hidden="true"><path d="M8 0a8 8 0 100 16A8 8 0 008 0zm0 1.5c1 1 1.8 3 2 5.5H6c.2-2.5 1-4.5 2-5.5zM1.6 7h3c.1-2 .6-3.8 1.4-5A6.5 6.5 0 001.6 7zm0 2a6.5 6.5 0 004.4 5c-.8-1.2-1.3-3-1.4-5zM6 9h4c-.2 2.5-1 4.5-2 5.5-1-1-1.8-3-2-5.5zm5.4 0h3a6.5 6.5 0 01-4.4 5c.8-1.2 1.3-3 1.4-5zm0-2c-.1-2-.6-3.8-1.4-5a6.5 6.5 0 014.4 5z"/></svg>www.<span class="url-accent">harborviewest</span>.com</li>
      </ul>
    </div>
  </section>
</main>
</body>
</html>
```